strength and conditioning business focused on helping people move more efficiently

I need a business card designed for a Philadelphia based company called Brsk Lft Motion (pronounced Brisk Lift). We offer fitness professional services with the idea of helping people feel better and move optimally. We do this by designing and walking through individualized programs as well as minor soft tissue work. Our perfect client would be athletes but we will be marketing to parents who have children that are active They remember their former athletic days and want to get as close as possible back to that feeling. Attached will be the official logo and logo formats. I would love for the design to communicate trustworthy and creative. I would also love for the design to be square with rounded edges.

Target Market(s)

Parents of athletic children
former athletes
athletes

Industry/Entity Type

Fitness

Contact Information for Business Card

Business: Brsk Lft Performance
Name: Coach Calvin Ashworth
Position: Strength and Conditioning Coach / Certified Personal Trainer
Contact: coach.ash@brsklft.com
Text: (555)204-7781

Font styles to use
Serif
Sans Serif

Colors
fbee38
fbee3e
0255a3
3176b5
ffffff

Requirements
Must have
• use of logo
Nice to have
• Square design
rounded edges

```html
<!DOCTYPE html>
<html lang="en">
<head>
<meta charset="utf-8">
<title>Brsk Lft Motion – Business Card</title>
<link href="https://fonts.googleapis.com/css2?family=Arimo:wght@400;700&display=swap" rel="stylesheet">
<style>
  :root {
    --navy: #0a2f80;
    --navy-deep: #082a73;
    --yellow: #fcd116;
    --ink: #222222;
    --white: #ffffff;
    --backdrop: #2b2b2b;
  }
  * { box-sizing: border-box; margin: 0; padding: 0; }
  html, body {
    width: 1200px; height: 859px; overflow: hidden;
    background: var(--backdrop);
    font-family: "Arimo", Arial, sans-serif;
  }
  .canvas { position: relative; width: 1200px; height: 859px; }
  .card {
    position: absolute; top: 208px;
    width: 446px; height: 446px;
    border-radius: 28px; overflow: hidden;
    box-shadow: 0 6px 18px rgba(0,0,0,0.45);
  }
  .card--front { left: 142px; background: var(--white); }
  .card--back { left: 626px; background: var(--navy); }

  .brand {
    position: absolute; left: 0; right: 0;
    display: flex; align-items: center; justify-content: center; gap: 12px;
    font-weight: 700; font-size: 38px; letter-spacing: 0.5px;
  }
  .brand__dot { width: 26px; height: 26px; border-radius: 50%; }
  .card--front .brand { top: 88px; color: var(--navy); }
  .card--front .brand__dot { background: var(--yellow); }
  .card--back .brand { top: 202px; color: var(--white); }
  .card--back .brand__dot { background: var(--yellow); }

  .person { position: absolute; top: 184px; left: 0; right: 0; text-align: center; }
  .person__name { font-size: 20px; font-weight: 700; color: var(--navy); }
  .person__first { color: var(--yellow); }
  .person__role { margin-top: 6px; font-size: 15px; line-height: 20px; color: var(--ink); }

  .contact-icons {
    position: absolute; top: 301px; left: 0; right: 0;
    display: flex; align-items: center; justify-content: center; gap: 5px;
  }
  .contact-icons__rule { width: 46px; height: 1.5px; background: var(--yellow); margin: 0 5px; }
  .contact-icons svg { width: 24px; height: 24px; display: block; }

  .contact { position: absolute; top: 336px; left: 0; right: 0; text-align: center;
    font-size: 16px; line-height: 21px; color: var(--ink); }

  .swoosh { position: absolute; left: 0; top: 0; width: 446px; height: 446px; }
</style>
</head>
<body>
<main class="canvas">
  <section class="card card--front" aria-label="Card front">
    <div class="brand"><span class="brand__dot"></span><span>Brsk Lft Motion</span></div>

    <div class="person">
      <p class="person__name"><span class="person__first">Coach Calvin</span> Ashworth</p>
      <p class="person__role">Strength and Conditioning Coach /<br>Certified Personal Trainer</p>
    </div>

    <div class="contact-icons">
      <span class="contact-icons__rule"></span>
      <svg viewBox="0 0 24 24" aria-label="Phone"><circle cx="12" cy="12" r="12" fill="#0a2f80"/><path d="M8.5 6.5l2 2-1.2 1.5a7 7 0 0 0 4.7 4.7l1.5-1.2 2 2-1.3 1.6c-4.6-.4-8.6-4.4-9-9z" fill="#fff"/></svg>
      <svg viewBox="0 0 24 24" aria-label="Email"><circle cx="12" cy="12" r="12" fill="#0a2f80"/><rect x="6" y="8" width="12" height="8.5" rx="1" fill="#fff"/><path d="M6.3 8.4L12 13l5.7-4.6" fill="none" stroke="#0a2f80" stroke-width="1.2"/></svg>
      <svg viewBox="0 0 24 24" aria-label="Website"><circle cx="12" cy="12" r="12" fill="#0a2f80"/><circle cx="12" cy="12" r="6" fill="none" stroke="#fff" stroke-width="1.4"/><ellipse cx="12" cy="12" rx="2.6" ry="6" fill="none" stroke="#fff" stroke-width="1.2"/><path d="M6 12h12" stroke="#fff" stroke-width="1.2"/></svg>
      <span class="contact-icons__rule"></span>
    </div>

    <div class="contact">
      <p>(555)204-7781</p>
      <p>coach.ash@brsklft.com</p>
      <p>www.brsklft.com</p>
    </div>

    <svg class="swoosh" viewBox="0 0 446 446" aria-hidden="true">
      <path d="M0 395 Q210 440 446 424 L446 446 L0 446 Z" fill="var(--navy)"/>
      <path d="M190 430 Q330 430 446 410 L446 420 Q330 438 190 432 Z" fill="var(--yellow)"/>
    </svg>
  </section>

  <section class="card card--back" aria-label="Card back">
    <div class="brand"><span class="brand__dot"></span><span>Brsk Lft Motion</span></div>
  </section>
</main>
</body>
</html>
```